PixelHarbor Rangers (Ledgerline Nova)
A website dedicated to crypto education. We are a new company focused on blockchain edutainment (education and interesting and entertaining content about the blockchain space). We want a fun, clean/minimalist and modern website that is made up of an education platform which could be a website in it’s own right. It will be the reference point for our users/community for all of our other blockchain based content in the PHR website ecosystem which will be covering; crypto news, digital asset investing (including a technical and fundamental analysis subscription service), blockchain business solutions and an NFT section that will cover creative art projects (art, music, gaming and more). To feature a logins and payment system which may need a shopping basket set up for tutorial/educational platform that is accessed via the website, NFT page with sub-categories: education and NFT and metaverse/virtual world and merchandise shopping page which is Web 3.0 enabled (able to link to a VeloPurse, Kindle Vault etc , digital asset education page featuring blog and newsletter subscriptions links, A social media page where people can access videos, podcasts and our presence on other platforms such as Chirplo, Snapmora, Huddlex, Wirepost etc.
Number of Pages Required
5+ page
Look and feel

```html
<!DOCTYPE html>
<html lang="en">
<head>
<meta charset="utf-8">
<title>PixelHarbor Rangers — Ledgerline Nova</title>
<link href="https://fonts.googleapis.com/css2?family=IBM+Plex+Sans:wght@400;500;600;700&display=swap" rel="stylesheet">
<style>
:root{
  --bg:#000;
  --ink:#fff;
  --muted:#c9c9d2;
  --purple:#7b2ff0;
  --purple-deep:#8a1fc7;
  --blue:#2fb0ea;
  --blue-deep:#1a86c8;
  --green:#6ad12f;
  --line:#2a2a33;
  --card:#07070b;
  --red:#e01a1a;
  --paid:#2f7d1c;
}
*{margin:0;padding:0;box-sizing:border-box}
html,body{width:1200px;height:4030px;overflow:hidden;background:var(--bg)}
body{position:relative;font-family:"IBM Plex Sans",Arial,sans-serif;color:var(--ink)}
.abs{position:absolute}
.center{text-align:center}
.h2{position:absolute;left:0;width:1200px;text-align:center;font-weight:700;font-size:44px;letter-spacing:1px;color:var(--ink)}
.read{color:var(--purple);font-weight:600;font-size:16px;letter-spacing:.3px}
.lorem{font-size:13.5px;line-height:22px;color:var(--muted)}

/* header */
.hero-bg{left:0;top:0;width:1200px;height:704px;background:radial-gradient(ellipse 70% 30% at 55% 78%,#3a3a44 0%,#17171c 40%,#000 75%)}
.logo{left:141px;top:70px;font-size:62px;font-weight:700;color:var(--purple);letter-spacing:6px;line-height:68px}
.phone{left:680px;top:36px;font-size:19px;font-weight:600;display:flex;align-items:center;gap:8px}
.cart{left:888px;top:34px}
.login{left:941px;top:27px;width:114px;height:44px;border-radius:22px;background:var(--purple);font-size:16px;font-weight:600;line-height:44px;text-align:center}
.nav{left:470px;top:95px;display:flex;gap:30px;font-size:12.5px;font-weight:500;letter-spacing:.3px}
.nav .on{border-bottom:2px solid var(--blue);padding-bottom:6px}
.hero-title{left:0;top:228px;width:1200px;font-size:76px;font-weight:700;letter-spacing:2px}
.hero-title .a{color:var(--blue)}.hero-title .b{color:var(--green)}
.hero-sub{left:0;top:340px;width:1200px;font-size:25px;font-weight:600;line-height:33px}

/* sprites */
.sprite{border-radius:6px}

/* ecosystem */
.eco{top:900px;width:190px;text-align:center}
.eco .blob{width:190px;height:180px;border-radius:50% 44% 50% 46%/54% 46% 54% 46%;display:flex;align-items:center;justify-content:center}
.eco .ring{width:140px;height:140px;border-radius:50%;border:5px solid #fff;display:flex;align-items:center;justify-content:center}
.eco .label{margin-top:22px;font-size:15.5px;font-weight:600;letter-spacing:.4px;line-height:22px}

/* education */
.net-bg{left:0;width:1200px}
.edu-card{top:1452px;width:296px;height:277px;border:1px solid var(--line);background:var(--card);padding:72px 18px 0}
.edu-card h3{font-size:16px;font-weight:600;letter-spacing:.3px;margin-bottom:14px}
.edu-card .read{display:block;margin-top:20px}
.date{top:1427px;width:63px;height:68px;background:var(--blue);text-align:center;font-size:16px;font-weight:500;line-height:22px;padding-top:12px}
.arrow{width:44px;height:44px;border:2px solid #fff;border-radius:50%;display:flex;align-items:center;justify-content:center}

/* nft */
.nft{top:1998px;width:330px;text-align:center}
.nft .disc{width:224px;height:224px;border-radius:50%;border:12px solid;margin:0 auto;background:#000;display:flex;align-items:center;justify-content:center}
.nft .art{width:130px;height:130px;border-radius:50%}
.nft h3{margin-top:20px;font-size:26px;font-weight:600}
.nft .lorem{margin-top:8px;font-size:12.5px;line-height:17px}
.nft .read{display:block;margin-top:18px}

/* features */
.feat{top:2615px;width:230px;text-align:center}
.feat h3{margin-top:22px;font-size:16px;font-weight:600;line-height:23px;letter-spacing:.3px}
.feat .lorem{margin-top:12px;font-size:13.5px;line-height:22px}
.feat .read{display:block;margin-top:18px}

/* courses */
.course{top:3086px;width:450px}
.course .photo{height:265px;position:relative}
.tag{position:absolute;left:16px;bottom:14px;width:84px;height:30px;font-size:15px;font-weight:600;text-align:center;line-height:30px}
.course h3{margin-top:33px;font-size:16px;font-weight:600;letter-spacing:.2px}
.course h3 span{color:var(--blue);margin-left:28px}
.course .lorem{margin-top:14px;font-size:13.5px;line-height:22px}
.cta{left:454px;top:3523px;width:292px;height:61px;border-radius:31px;background:var(--purple);font-size:21px;font-weight:600;letter-spacing:.5px;line-height:61px;text-align:center}

/* footer */
.foot-bg{left:0;top:3647px;width:1200px;height:383px;background:linear-gradient(180deg,#000 0%,#0d0d12 60%,#1b1b22 100%);border-top:1px solid #1b1b22}
.flogo{left:142px;top:3745px;font-size:92px;font-weight:700;color:var(--purple);letter-spacing:8px;line-height:100px}
.pay{top:3897px;width:50px;height:36px;border-radius:4px;background:#fff;color:#333;font-size:9px;font-weight:600;display:flex;align-items:center;justify-content:center}
.links h4{font-size:19px;font-weight:600;color:var(--blue);letter-spacing:.5px;margin-bottom:18px}
.links li{list-style:none;font-size:13px;line-height:28.5px}
.wallet{font-size:17px;font-weight:500;display:flex;align-items:center;gap:10px}
.social{top:3872px;width:40px;height:40px;border-radius:50%;font-size:9px;font-weight:600;display:flex;align-items:center;justify-content:center}
.signup{left:776px;top:3948px;width:285px;height:42px;border-radius:21px;background:#fff;overflow:hidden}
.signup .field{position:absolute;left:32px;top:0;line-height:42px;color:#333;font-size:12.5px}
.signup .btn{position:absolute;right:0;top:0;width:105px;height:42px;border-radius:21px;background:var(--purple);color:#fff;font-size:13px;font-weight:600;line-height:42px;text-align:center}
.copy{left:142px;top:3980px;font-size:11.5px;color:#ddd}
</style>
</head>
<body>

<!-- Hero -->
<div class="abs hero-bg" role="img" aria-label="Dark particle wave landscape"></div>
<div class="abs logo">PHR</div>
<div class="abs phone">
  <svg width="18" height="18" viewBox="0 0 24 24"><path fill="#2fb0ea" d="M6.6 10.8a15.1 15.1 0 0 0 6.6 6.6l2.2-2.2c.3-.3.7-.4 1-.2 1.1.4 2.3.6 3.6.6.6 0 1 .4 1 1V20c0 .6-.4 1-1 1A17 17 0 0 1 3 4c0-.6.4-1 1-1h3.5c.6 0 1 .4 1 1 0 1.3.2 2.5.6 3.6.1.3 0 .7-.2 1z"/></svg>
  +1 555 010 2040
</div>
<svg class="abs cart" width="40" height="32" viewBox="0 0 40 32">
  <path d="M2 4h5l4 16h17l4-11H10" fill="none" stroke="#fff" stroke-width="2.2" stroke-linejoin="round"/>
  <circle cx="13" cy="26" r="2.5" fill="#fff"/><circle cx="26" cy="26" r="2.5" fill="#fff"/>
  <circle cx="33" cy="7" r="7" fill="#7b2ff0"/><text x="33" y="10.5" font-size="10" fill="#fff" text-anchor="middle" font-family="IBM Plex Sans,sans-serif">0</text>
</svg>
<div class="abs login">LOGIN</div>
<nav class="abs nav">
  <span class="on">HOME</span><span>CRYPTO NEWS</span><span>DIGITAL ASSET INVESTING</span><span>MERCHANDISE</span><span>NFT PROJECTS</span>
</nav>
<h1 class="abs hero-title center"><span class="a">LEDGERLINE</span> <span class="b">NOVA</span></h1>
<p class="abs hero-sub center">Sed ut perspiciatis unde omnis iste natus error<br>sit voluptatem accusantium</p>
<svg class="abs" style="left:551px;top:439px" width="98" height="98" viewBox="0 0 98 98">
  <circle cx="49" cy="49" r="45" fill="none" stroke="#fff" stroke-width="6"/>
  <path d="M38 30l30 19-30 19z" fill="#fff"/>
</svg>

<!-- Ecosystem -->
<div class="abs sprite" style="left:10px;top:735px;width:124px;height:110px;background:#e020e0" role="img" aria-label="Pixel space invader character"></div>
<h2 class="h2" style="top:778px">PHR ECOSYSTEM</h2>

<div class="abs eco" style="left:143px">
  <div class="blob" style="background:linear-gradient(135deg,#b02ad8,#6a16a8)"><div class="ring">
    <svg width="62" height="62" viewBox="0 0 62 62" fill="none" stroke="#fff" stroke-width="3"><rect x="8" y="10" width="46" height="42" rx="3"/><path d="M16 20h14v12H16zM36 20h10M36 27h10M16 40h30M16 46h30"/></svg>
  </div></div>
  <div class="label">CRYPTO NEWS</div>
</div>
<div class="abs eco" style="left:382px">
  <div class="blob" style="background:linear-gradient(135deg,#36b8ee,#1470b0)"><div class="ring">
    <svg width="62" height="62" viewBox="0 0 62 62" fill="none" stroke="#fff" stroke-width="3"><rect x="20" y="6" width="22" height="50" rx="4"/><circle cx="31" cy="31" r="7"/><path d="M4 24h14M4 38h14M44 24h14M44 38h14"/></svg>
  </div></div>
  <div class="label">DIGITAL ASSET<br>INVESTING</div>
</div>
<div class="abs eco" style="left:625px">
  <div class="blob" style="background:linear-gradient(135deg,#29a2e0,#155f9a)"><div class="ring">
    <svg width="62" height="62" viewBox="0 0 62 62" fill="none" stroke="#fff" stroke-width="3"><rect x="22" y="6" width="18" height="16"/><rect x="6" y="24" width="18" height="16"/><rect x="38" y="24" width="18" height="16"/><rect x="22" y="42" width="18" height="16"/></svg>
  </div></div>
  <div class="label">BLOCKCHAIN<br>BUSINESS SOLUTIONS</div>
</div>
<div class="abs eco" style="left:866px">
  <div class="blob" style="background:linear-gradient(135deg,#7ee03a,#3a9a18)"><div class="ring">
    <svg width="70" height="70" viewBox="0 0 70 70"><polygon points="35,5 61,20 61,50 35,65 9,50 9,20" fill="none" stroke="#fff" stroke-width="3"/><text x="35" y="42" text-anchor="middle" font-size="19" fill="#fff" font-family="IBM Plex Sans,sans-serif">NFT</text></svg>
  </div></div>
  <div class="label">NFT</div>
</div>

<!-- Digital asset education -->
<div class="abs net-bg" style="top:1236px;height:564px;background:radial-gradient(ellipse 60% 45% at 50% 30%,#26262d 0%,#101014 45%,#000 80%)" role="img" aria-label="Faint network of connected points"></div>
<h2 class="h2" style="top:1300px;color:#b8b8c0">DIGITAL ASSET EDUCATION</h2>
<div class="abs sprite" style="left:55px;top:1318px;width:130px;height:115px;background:#f06a1e" role="img" aria-label="Pixel tiger character"></div>
<div class="abs sprite" style="left:1066px;top:1446px;width:88px;height:60px;background:#5fd42a" role="img" aria-label="Pixel creature character"></div>

<div class="abs edu-card" style="left:142px"><h3>NEMO ENIM IPSALUPTATEM</h3><p class="lorem">Lorem ipsum dolor sit amet, consectetur adipiscing elit, sed do eiusmod tempor incididunt ut labore et dolore magna aliqua ipsum suspendisse ulavi</p><span class="read">READ MORE</span></div>
<div class="abs edu-card" style="left:452px"><h3>NEQUE PORRO QUISQUAM</h3><p class="lorem">Lorem ipsum dolor sit amet, consectetur adipiscing elit, sed do eiusmod tempor incididunt ut labore et dolore magna aliqua ipsum suspendisse ulavi</p><span class="read">READ MORE</span></div>
<div class="abs edu-card" style="left:761px"><h3>QUIS AUTEM VEL EUM IURE</h3><p class="lorem">Lorem ipsum dolor sit amet, consectetur adipiscing elit, sed do eiusmod tempor incididunt ut labore et dolore magna aliqua ipsum suspendisse ulavi</p><span class="read">READ MORE</span></div>
<div class="abs date" style="left:161px">FEB<br>2022</div>
<div class="abs date" style="left:471px">FEB<br>2022</div>
<div class="abs date" style="left:780px">FEB<br>2022</div>
<div class="abs arrow" style="left:56px;top:1570px"><svg width="14" height="18" viewBox="0 0 14 18"><path d="M10 2L3 9l7 7" fill="none" stroke="#fff" stroke-width="2.5"/></svg></div>
<div class="abs arrow" style="left:1100px;top:1570px"><svg width="14" height="18" viewBox="0 0 14 18"><path d="M4 2l7 7-7 7" fill="none" stroke="#fff" stroke-width="2.5"/></svg></div>

<!-- NFT creative art -->
<div class="abs net-bg" style="top:1800px;height:500px;background:radial-gradient(ellipse 55% 30% at 50% 10%,#1d1d23 0%,#000 70%)" role="img" aria-label="Faint network of connected points"></div>
<h2 class="h2" style="top:1868px">NFT CREATIVE ART PROJECTS</h2>
<div class="abs sprite" style="left:1064px;top:1922px;width:122px;height:130px;background:linear-gradient(#1a2f55,#e8e8e8)" role="img" aria-label="Pixel penguin character"></div>
<svg class="abs" style="left:114px;top:2078px" width="36" height="64" viewBox="0 0 36 64"><path d="M32 2L4 32l28 30" fill="none" stroke="#fff" stroke-width="2"/></svg>
<svg class="abs" style="left:1050px;top:2078px" width="36" height="64" viewBox="0 0 36 64"><path d="M4 2l28 30L4 62" fill="none" stroke="#fff" stroke-width="2"/></svg>

<div class="abs nft" style="left:135px">
  <div class="disc" style="border-color:var(--purple)"><div class="art" style="background:radial-gradient(#c8863a,#2a1a10)" role="img" aria-label="Pixel artist character illustration"></div></div>
  <h3>ART</h3><p class="lorem">Lorem ipsum dolor sit amet, consectetur<br>adipiscing elit, sed do eiusmod tempor<br>incididunt ut labore et dolore magna</p><span class="read">READ MORE</span>
</div>
<div class="abs nft" style="left:435px">
  <div class="disc" style="border-color:var(--blue)"><div class="art" style="background:radial-gradient(#d0527a,#2a1018)" role="img" aria-label="Pixel musician character illustration"></div></div>
  <h3>MUSIC</h3><p class="lorem">Lorem ipsum dolor sit amet, consectetur<br>adipiscing elit, sed do eiusmod tempor<br>incididunt ut labore et dolore magna</p><span class="read">READ MORE</span>
</div>
<div class="abs nft" style="left:735px">
  <div class="disc" style="border-color:var(--green)"><div class="art" style="background:radial-gradient(#c02828,#1a0c0c)" role="img" aria-label="Pixel robot character illustration"></div></div>
  <h3>GAMING</h3><p class="lorem">Lorem ipsum dolor sit amet, consectetur<br>adipiscing elit, sed do eiusmod tempor<br>incididunt ut labore et dolore magna</p><span class="read">READ MORE</span>
</div>

<!-- Features -->
<h2 class="h2" style="top:2503px">FEATURES</h2>
<div class="abs feat" style="left:123px">
  <svg width="64" height="64" viewBox="0 0 64 64" fill="none" stroke="#2fb0ea" stroke-width="2"><circle cx="26" cy="26" r="18"/><circle cx="38" cy="38" r="18"/><circle cx="38" cy="38" r="11"/></svg>
  <h3>EARN TOKENS</h3><p class="lorem">Lorem ipsum dolor sit amet, consectetur adipiscing elit, sed do eiusmod tempor incididunt</p><span class="read">READ MORE</span>
</div>
<div class="abs feat" style="left:365px">
  <svg width="64" height="64" viewBox="0 0 64 64" fill="none" stroke="#2fb0ea" stroke-width="2"><circle cx="32" cy="26" r="20"/><polygon points="32,14 35.5,22 44,22.5 37.5,28 39.5,36.5 32,32 24.5,36.5 26.5,28 20,22.5 28.5,22"/><path d="M22 44l-4 16 14-6 14 6-4-16"/></svg>
  <h3>ACHIEVING LEVELS</h3><p class="lorem">Lorem ipsum dolor sit amet, consectetur adipiscing elit, sed do eiusmod tempor incididunt</p><span class="read">READ MORE</span>
</div>
<div class="abs feat" style="left:613px">
  <svg width="64" height="64" viewBox="0 0 64 64" fill="none" stroke="#2fb0ea" stroke-width="2"><circle cx="32" cy="32" r="26"/><circle cx="32" cy="24" r="6"/><circle cx="18" cy="32" r="5"/><circle cx="46" cy="32" r="5"/><path d="M22 48c0-8 20-8 20 0M10 46c0-6 14-6 14 0M40 46c0-6 14-6 14 0"/></svg>
  <h3>CONTRIBUTING TO THE<br>COMMUNITY ECOSYSTEM</h3><p class="lorem">Lorem ipsum dolor sit amet, consectetur adipiscing elit,</p><span class="read">READ MORE</span>
</div>
<div class="abs feat" style="left:858px">
  <svg width="64" height="64" viewBox="0 0 64 64" fill="none" stroke="#2fb0ea" stroke-width="2"><rect x="6" y="6" width="18" height="18" rx="4"/><circle cx="48" cy="15" r="9"/><rect x="6" y="40" width="18" height="18" rx="4"/><rect x="40" y="40" width="18" height="18" rx="4"/><path d="M24 15h15M15 24v16M48 24v16M24 49h16"/></svg>
  <h3>MARKETING VIA<br>SOCIAL MEDIA</h3><p class="lorem">Lorem ipsum dolor sit amet, consectetur adipiscing elit,</p><span class="read">READ MORE</span>
</div>

<!-- Courses -->
<h2 class="h2" style="top:2977px">PRACTICAL EDUCATIONAL COURSES</h2>
<div class="abs sprite" style="left:1052px;top:2947px;width:76px;height:76px;background:#2fa8e6" role="img" aria-label="Pixel space invader character"></div>
<div class="abs arrow" style="left:56px;top:3195px"><svg width="14" height="18" viewBox="0 0 14 18"><path d="M10 2L3 9l7 7" fill="none" stroke="#fff" stroke-width="2.5"/></svg></div>
<div class="abs arrow" style="left:1100px;top:3195px"><svg width="14" height="18" viewBox="0 0 14 18"><path d="M4 2l7 7-7 7" fill="none" stroke="#fff" stroke-width="2.5"/></svg></div>

<div class="abs course" style="left:142px">
  <div class="photo" style="background:linear-gradient(120deg,#d8e6f2 0%,#6aa2d8 40%,#0c3f8a 75%,#041a40 100%)" role="img" aria-label="Hands typing on a laptop with digital data overlay">
    <svg style="position:absolute;right:22px;bottom:16px" width="44" height="44" viewBox="0 0 44 44"><circle cx="22" cy="22" r="19" fill="none" stroke="#fff" stroke-width="3"/><path d="M17 13l13 9-13 9z" fill="#fff"/></svg>
    <span class="tag" style="background:var(--red)">FREE</span>
  </div>
  <h3>NEMO ENIM IPSALUPTATXERCIT<span>10% OFF</span></h3>
  <p class="lorem">Lorem ipsum dolor sit amet, consectetur adipiscing elit, sed do eiusmod tempor incididunt ut labore et dolore magna aliqua</p>
</div>
<div class="abs course" style="left:609px">
  <div class="photo" style="background:linear-gradient(120deg,#e8e4e0 0%,#b8a494 40%,#5a4a40 75%,#2a2020 100%)" role="img" aria-label="Hand reaching toward a laptop with trading chart overlay">
    <svg style="position:absolute;right:20px;bottom:16px" width="44" height="44" viewBox="0 0 44 44" fill="none" stroke="#fff" stroke-width="3"><circle cx="22" cy="20" r="4"/><path d="M22 24v16M14 28a11 11 0 1 1 16 0M9 34a18 18 0 1 1 26 0"/></svg>
    <span class="tag" style="background:var(--paid)">PAID</span>
  </div>
  <h3>EQUE PORRO QUISQUAM ESTQUI DOLOREM<span>50% OFF</span></h3>
  <p class="lorem">Lorem ipsum dolor sit amet, consectetur adipiscing elit, sed do eiusmod tempor incididunt ut labore et dolore magna aliqua</p>
</div>
<div class="abs cta">CHECK YOUR RESULT</div>

<!-- Footer -->
<footer>
  <div class="abs foot-bg"></div>
  <div class="abs flogo">PHR</div>
  <div class="abs pay" style="left:142px">Vantapay</div>
  <div class="abs pay" style="left:206px">Circlo</div>
  <div class="abs pay" style="left:270px">Findora</div>
  <div class="abs pay" style="left:334px">Amerigo</div>
  <div class="abs pay" style="left:398px">Paywell</div>

  <div class="abs links" style="left:541px;top:3740px">
    <h4>LINKS</h4>
    <ul><li>Home</li><li>Crypto news</li><li>Digital asset investing</li><li>Merchandise</li><li>NFT projects</li></ul>
  </div>

  <div class="abs wallet" style="left:776px;top:3775px;flex-direction:column;gap:6px;font-size:12px;color:#ccc">
    <span style="width:40px;height:40px;border-radius:50%;background:#f0821e;display:block"></span>VELOPURSE
  </div>
  <div class="abs wallet" style="left:903px;top:3774px">
    <span style="width:34px;height:34px;border-radius:8px;background:#fff;display:block"></span>Kindle Vault
  </div>

  <div class="abs social" style="left:778px;background:#1d9bf0">Chirplo</div>
  <div class="abs social" style="left:823px;background:#d6249f">Snapmora</div>
  <div class="abs social" style="left:869px;background:#5865f2">Huddlex</div>
  <div class="abs social" style="left:914px;background:#2aa3dc">Wirepost</div>

  <div class="abs signup"><span class="field">Enter Email</span><span class="btn">SIGN UP</span></div>
  <p class="abs copy">Copyright © 2022 pixelharbor rangers. All rights reserved &nbsp;| &nbsp;Terms of use &nbsp;| &nbsp;Privacy policy &nbsp;| &nbsp;Site map</p>
</footer>

</body>
</html>
```